The Harbourlight Dental centre, the Zorvik of dentistry

New concept of running a dental practice by having a walk in practice
WE ARE A HUSBAND AND WIFE TEAM

Really modern and sophisticated, we want it to feel different from the traditional dental practice.
we want it split into different pages:CONTACT US
LOCATION: Information about our location since patients often confuse us with the practice across the road
ABOUT US:
Opening hours - & 7 Days, We offer a weekend service
WALK IN: We offer a walk in service for dental treatments
TREATMENTS we offer

DENTAL ADVICE: Free dentist advise call back- So a dentist will call you back for free to discuss

Target Market(s)

Everyone

Industry/Entity Type

Dental

Coding

Coded - Design and coding required

Number of Pages Required

5+ page

Requirements
Must have
• First page
• * changing pictures
• *opening times
• * our walk in concept I.e. no appointment needed
• *logo
• * links in to clinic tidal (online booking system in Australia)
• * address /phone number/email
• * possible videos
• Second page
• meet the team
• third page
• dental treatments/walk in treatments
• fourth page
• dental advice with vid larko videos
• Fifth page
• contact us/maps/ we get confused with the dental practice across the road
• We would also like a giving back page. In this please include the photo's below of our dental mission in Guatemala, where by we did treatment for patients as part of a charity.
Nice to have
• Changing pictures on the home screen
• videos linked to home page

```html
<!DOCTYPE html>
<html lang="en">
<head>
<meta charset="utf-8">
<title>The Harbourlight Dental Centre</title>
<link href="https://fonts.googleapis.com/css2?family=Open+Sans:wght@300;400;600;700&display=swap" rel="stylesheet">
<style>
:root{
  --blue:#00b4ef;
  --green:#8dc63f;
  --ink:#3a3a3a;
  --muted:#6b6b6b;
  --light:#f3f3f3;
  --line:#e2e2e2;
  --dark:#3b3b3b;
  --white:#ffffff;
}
*{box-sizing:border-box;margin:0;padding:0}
html,body{width:687px;height:1200px;overflow:hidden}
body{font-family:'Open Sans',sans-serif;color:var(--ink);background:var(--white);position:relative}
.wrap{width:534px;margin:0 auto;position:relative}
.topbar{height:23px;border-bottom:1px solid var(--line);font-size:6px;color:var(--muted)}
.topbar .wrap{display:flex;justify-content:space-between;align-items:center;height:23px}
.topbar span{display:flex;align-items:center;gap:3px}
.topbar svg{width:6px;height:6px;fill:var(--muted)}
.header{height:58px}
.header .wrap{display:flex;justify-content:space-between;align-items:center;height:58px}
.brand{display:flex;align-items:center;gap:6px}
.brand-mark{width:24px;height:24px;border-radius:50%;background:var(--blue)}
.brand-name{font-size:11px;font-weight:700;color:var(--green);line-height:1.1}
.brand-name small{display:block;font-size:5px;letter-spacing:1px;font-weight:700;color:var(--green)}
.nav{display:flex;gap:17px;font-size:6.3px;color:var(--muted)}
.nav .active{color:var(--blue);text-decoration:underline}
.hero{height:229px;position:relative;background:linear-gradient(90deg,#f6f3dc 0%,#efe7c8 35%,#d9b994 60%,#b89a7c 80%,#9ab37a 100%)}
.hero-title{position:absolute;left:76px;top:58px;font-size:18px;font-weight:300;color:#222;line-height:1.15}
.hero-arrow{position:absolute;top:107px;width:16px;height:16px;background:#8a8a8a;display:flex;align-items:center;justify-content:center}
.hero-arrow svg{width:8px;height:8px;fill:#fff}
.hero-arrow.prev{left:0}.hero-arrow.next{right:0}
.bands{display:flex;height:41px}
.band-blue{width:343px;background:var(--blue);color:#fff;font-size:7.3px;font-weight:700;padding:10px 0 0 76px;line-height:1.45}
.band-green{flex:1;background:var(--green);color:#fff;font-size:11.5px;font-weight:700;display:flex;align-items:center;justify-content:center}
.welcome{height:174px;padding-top:30px}
.welcome .wrap{display:flex;gap:12px}
.video{width:139px;height:110px;background:linear-gradient(135deg,#2c3340,#51607a 60%,#3a3f4a);position:relative;flex:none}
.video .play{position:absolute;left:59px;top:44px;width:20px;height:20px;border-radius:50%;background:var(--blue);border:2px solid #fff;display:flex;align-items:center;justify-content:center}
.video .play svg{width:8px;height:8px;fill:#fff}
.welcome h1{font-size:17.5px;font-weight:400;color:var(--green);margin-top:-3px}
.welcome p{font-size:6.2px;line-height:1.8;color:var(--muted);margin-top:5px}
.callout{margin-top:10px;border:1px solid var(--blue);padding:10px 16px;font-size:9px;color:var(--blue);line-height:1.4}
.callout strong{font-weight:400;font-size:11px;display:block}
.services{height:316px;background:var(--light);padding-top:20px}
.section-title{text-align:center;font-size:17.5px;font-weight:400;color:var(--green)}
.grid{display:grid;grid-template-columns:repeat(4,126px);gap:10px 10.6px;margin-top:14px}
.tile-img{height:87px}
.tile-label{height:22px;background:var(--blue);color:#fff;font-size:8.6px;font-weight:600;padding:5px 8px}
.testimonials{height:134px;text-align:center;padding-top:25px}
.testimonials h2{font-size:22px;font-weight:700;color:#d3d3d3;letter-spacing:.5px}
.quote{font-size:11.5px;color:var(--ink);margin-top:5px}
.quote b{color:#bbb;font-size:16px;font-weight:700;vertical-align:-3px}
.author{font-size:8px;margin-top:6px}
.dots{display:flex;justify-content:center;gap:7px;margin-top:10px}
.dots i{width:5px;height:5px;border-radius:50%;background:#bbb}
.dots i.on{background:var(--green)}
.contact{height:142px;display:flex}
.map{width:343px;background:linear-gradient(135deg,#dcdcdc,#c8c8c8 50%,#d6d6d6)}
.form{flex:1;background:#ececec;padding:18px 0 0 29px}
.form h3{font-size:13.5px;font-weight:400}
.fields{display:grid;grid-template-columns:105px 105px;gap:7px 6px;margin-top:9px}
.field{height:21px;background:#fff;font-size:6.3px;color:var(--muted);padding:6px 10px}
.submit{background:var(--dark);color:#fff;text-align:center}
.footer{height:83px;background:var(--dark);color:#ddd;font-size:6.2px}
.foot-top{display:flex;align-items:center;height:37px;border-bottom:1px solid #555;gap:28px}
.foot-top span{display:flex;align-items:center;gap:5px}
.foot-top svg{width:7px;height:7px;fill:#ccc}
.socials{margin-left:auto;display:flex;gap:8px}
.socials i{width:5px;height:5px;border-radius:50%;background:#999}
.foot-bottom{display:flex;justify-content:space-between;padding-top:10px}
.foot-links{font-size:5.3px;line-height:2.6;color:#ccc}
.booking{display:flex;align-items:center;gap:12px;font-size:5.3px;color:#ccc}
.booking-name{font-size:11px;color:#aaa;font-weight:400;display:flex;align-items:center;gap:4px}
.booking-name i{width:9px;height:9px;background:#aaa}
</style>
</head>
<body>
<div class="topbar"><div class="wrap">
  <span><svg viewBox="0 0 10 10"><path d="M5 0a3.5 3.5 0 0 0-3.5 3.5C1.5 6 5 10 5 10s3.5-4 3.5-6.5A3.5 3.5 0 0 0 5 0zm0 5a1.5 1.5 0 1 1 0-3 1.5 1.5 0 0 1 0 3z"/></svg>Suite 7, 18 Ternwood Parade, Kellsbrook, WA 6071,</span>
  <span><svg viewBox="0 0 10 10"><path d="M2 0l2 2.5-1 1.5a6 6 0 0 0 3 3l1.5-1L10 8l-1.5 2C4 10 0 6 0 1.5z"/></svg>08 6270 3158</span>
  <span><svg viewBox="0 0 10 10"><path d="M0 2h10v6H0zM0 2l5 3.5L10 2"/></svg>hello@harbourlightdental.example</span>
  <span><svg viewBox="0 0 10 10"><circle cx="5" cy="5" r="5"/></svg>OPEN 8 AM TO 8PM 7 DAYS A WEEK</span>
</div></div>

<header class="header"><div class="wrap">
  <div class="brand"><div class="brand-mark"></div><div class="brand-name">The Harbourlight<small>DENTAL CENTRE</small></div></div>
  <nav class="nav"><span class="active">Home</span><span>Meet the Team</span><span>Dental Treatments/Walk-in Treatments</span><span>Dental Advice</span><span>Contact us</span></nav>
</div></header>

<section class="hero" role="img" aria-label="Smiling woman in warm sunlight, slideshow photo">
  <div class="hero-title">Aenean hendrerit<br>velit vitae nibh</div>
  <div class="hero-arrow prev"><svg viewBox="0 0 10 10"><path d="M6 1L2 5l4 4V6h3V4H6z"/></svg></div>
  <div class="hero-arrow next"><svg viewBox="0 0 10 10"><path d="M4 1l4 4-4 4V6H1V4h3z"/></svg></div>
</section>

<div class="bands">
  <div class="band-blue">WE UNDERSTAND THAT EVERYONE HAS A BUSY LIFE AND WE<br>WANT DENTAL TREATMENT TO BE ACCESSIBLE FOR ALL.</div>
  <div class="band-green">No Appointment Needed!</div>
</div>

<section class="welcome"><div class="wrap">
  <div class="video" role="img" aria-label="Video still of a dentist treating a patient"><div class="play"><svg viewBox="0 0 10 10"><path d="M2 1l7 4-7 4z"/></svg></div></div>
  <div>
    <h1>Welcome to The Harbourlight Dental Centre</h1>
    <p>Your general and cosmetic dentist in the heart of vibrant Kellsbrook. Whether it's cosmetic hygiene treatment, tooth whitening, or botox facial rejuvenation.<br>Located within the busy medical centrewith free parking all around.</p>
    <div class="callout">Please call or pop in and one of our helpful team will be only too happy to help for<strong>ALL YOUR DENTAL NEEDS.</strong></div>
  </div>
</div></section>

<section class="services">
  <h2 class="section-title">Our Services</h2>
  <div class="wrap grid">
    <div><div class="tile-img" role="img" aria-label="Child having a tooth extracted" style="background:linear-gradient(135deg,#c9b6a8,#6e5e8a)"></div><div class="tile-label">Extractions</div></div>
    <div><div class="tile-img" role="img" aria-label="Dentist showing dentures to a patient" style="background:linear-gradient(135deg,#e8e2dc,#8aa2c0)"></div><div class="tile-label">Dentures</div></div>
    <div><div class="tile-img" role="img" aria-label="Close-up of a filled molar" style="background:linear-gradient(135deg,#c86a6a,#e8d6c8)"></div><div class="tile-label">Fillings</div></div>
    <div><div class="tile-img" role="img" aria-label="Patient in dental chair for root canal" style="background:linear-gradient(135deg,#d8dcdc,#8f9a9a)"></div><div class="tile-label">Root Canal Treatment</div></div>
    <div><div class="tile-img" role="img" aria-label="Gum examination with dental tools" style="background:linear-gradient(135deg,#5a3a3a,#b07070)"></div><div class="tile-label">Periodontal Treatment</div></div>
    <div><div class="tile-img" role="img" aria-label="Dental model with crowns and bridge" style="background:linear-gradient(135deg,#8ea0b4,#e6d2bc)"></div><div class="tile-label">Crowns and Bridges</div></div>
    <div><div class="tile-img" role="img" aria-label="Smile before and after whitening" style="background:linear-gradient(135deg,#c2505a,#f0e6e0)"></div><div class="tile-label">Teeth Whitening</div></div>
    <div><div class="tile-img" role="img" aria-label="Woman with smooth skin after facial treatment" style="background:linear-gradient(135deg,#f2ece6,#d6b48a)"></div><div class="tile-label">Facial Aesthetics</div></div>
  </div>
</section>

<section class="testimonials">
  <h2>TESTIMONIALS</h2>
  <p class="quote"><b>&ldquo;</b> Etiam quis magna nec odio sagittis pretium id eget risus eget fermentum magna arcu. <b>&rdquo;</b></p>
  <p class="author">Mara Elden, City</p>
  <div class="dots"><i class="on"></i><i></i><i></i><i></i></div>
</section>

<section class="contact">
  <div class="map" role="img" aria-label="Grey map showing the clinic location"></div>
  <div class="form">
    <h3>Contact Us</h3>
    <div class="fields">
      <div class="field">First Name</div><div class="field">Last Name</div>
      <div class="field">Phone</div><div class="field">Email</div>
      <div class="field">City</div><div class="field submit">SUBMIT</div>
    </div>
  </div>
</section>

<footer class="footer"><div class="wrap">
  <div class="foot-top">
    <span><svg viewBox="0 0 10 10"><path d="M5 0a3.5 3.5 0 0 0-3.5 3.5C1.5 6 5 10 5 10s3.5-4 3.5-6.5A3.5 3.5 0 0 0 5 0z"/></svg>Suite 7, 18 Ternwood Parade, Kellsbrook, WA 6071</span>
    <span><svg viewBox="0 0 10 10"><path d="M2 0l2 2.5-1 1.5a6 6 0 0 0 3 3l1.5-1L10 8l-1.5 2C4 10 0 6 0 1.5z"/></svg>Call Now: 08 6270 3158</span>
    <span><svg viewBox="0 0 10 10"><path d="M0 2h10v6H0z"/></svg>Email: hello@harbourlightdental.example</span>
    <div class="socials"><i></i><i></i><i></i><i></i></div>
  </div>
  <div class="foot-bottom">
    <div class="foot-links">Home &nbsp;|&nbsp; Meet the Team &nbsp;|&nbsp; Dental Treatments/Walk-in Treatments &nbsp;|&nbsp; Dental Advice &nbsp;|&nbsp; Contact us<br>Copyright &copy; 2016 The Harbourlight Dental centre. &nbsp;All rights reserved.</div>
    <div class="booking">Appointment Booking <span class="booking-name"><i></i>clinic tidal</span></div>
  </div>
</div></footer>
</body>
</html>
```